Thank You For Shopping / Hair Care Tips

I need “Thank You For Shopping”
Post cards made for my hair business !
I added pictures of post cards that I really like . I also added my LunaKova Wigs logo for you guys to use

I want the backside of the flyer to have hair care tips !
I want people to have full directions on how to care for their wigs

Target Market(s)

Im marking to young woman to older middle aged woman
Ages 23-66 . I want my flyer to look mature And classy

Industry/Entity Type

Hair And Beauty

Font styles to use
Serif
Script

Colors
e34699
e34298
e34398

Requirements
Must have
• The flyer must have the Instagram logo with my Instagram name next to it @luna.kova.wigs__
• Also it must have my “Luna Kova Wigs” logo that I’ve uploaded in the pictures section .
• Flyer had to be two sides . One side “ thank you for shopping “ side two “hair care tips”
• My website must be on the flyer - www.lunakovawigs.example
• The flyer must match the colors of my logo
• All white . With the pink and glitter sliver you see on my logo
Nice to have
• Nice to have a glitter border
Should not have
• The flyer should not have different colors that don’t match my logo
• It shouldn’t be made without having my Instagram or website on the flyer

```html
<!DOCTYPE html>
<html lang="en">
<head>
<meta charset="utf-8">
<title>LunaKova Wigs – Thank You Card and Hair Care Tips</title>
<link rel="stylesheet" href="https://fonts.googleapis.com/css2?family=Yellowtail&family=Quicksand:wght@500;600&display=swap">
<style>
  :root {
    --pink: #e34699;
    --ink: #3a3a3e;
    --page: #f2f2f4;
    --card-light: #ffffff;
    --card-shade: #e6e7ea;
    --silver-light: #d9d9dc;
    --silver-mid: #a9aab0;
    --silver-dark: #7d7e84;
  }
  * { box-sizing: border-box; margin: 0; padding: 0; }
  html, body { width: 1200px; height: 683px; overflow: hidden; background: var(--page); }
  .canvas {
    position: relative; width: 1200px; height: 683px;
    display: flex; justify-content: center; align-items: center; gap: 40px;
  }
  .postcard {
    position: relative; width: 560px; height: 400px; padding: 13px;
    background: linear-gradient(135deg, var(--silver-light), var(--silver-mid) 40%, var(--silver-light) 60%, var(--silver-dark));
    box-shadow: 0 6px 18px rgba(0,0,0,0.12);
  }
  .postcard__face {
    position: relative; width: 100%; height: 100%;
    background: linear-gradient(160deg, var(--card-light) 0%, #f4f4f6 45%, var(--card-shade) 100%);
    overflow: hidden;
  }
  .brand-mark {
    position: absolute; top: 36px; right: 40px;
    font-family: "Quicksand", sans-serif; font-weight: 600;
    font-size: 24px; color: var(--pink); letter-spacing: 0.5px; white-space: nowrap;
  }
  .thanks-heading {
    position: absolute; left: 50px; top: 118px;
    font-family: "Yellowtail", cursive; font-weight: 400;
    font-size: 74px; line-height: 1; color: var(--pink); white-space: nowrap;
  }
  .thanks-heading__line { display: block; }
  .thanks-heading__line--indent { padding-left: 50px; }
  .tips-heading {
    position: absolute; left: 46px; top: 28px;
    font-family: "Yellowtail", cursive; font-weight: 400;
    font-size: 58px; line-height: 1.1; color: var(--pink); white-space: nowrap;
  }
  .tips-list {
    position: absolute; left: 58px; top: 118px; list-style: none;
    font-family: "Quicksand", sans-serif; font-weight: 500;
    font-size: 13.5px; line-height: 20px; color: var(--ink); white-space: nowrap;
  }
  .tips-list__gap { margin-top: 20px; }
  .contact {
    position: absolute; font-family: "Quicksand", sans-serif; font-weight: 500;
    font-size: 12.5px; color: var(--pink); text-transform: uppercase; white-space: nowrap;
  }
  .contact--social { left: 62px; bottom: 24px; display: flex; align-items: center; gap: 6px; }
  .contact__dot { width: 14px; height: 14px; border-radius: 50%; border: 2px solid var(--silver-dark); }
  .contact--web { right: 36px; bottom: 56px; }
</style>
</head>
<body>
<main class="canvas">
  <section class="postcard postcard--front">
    <div class="postcard__face">
      <div class="brand-mark">Luna Kova Wigs</div>
      <h1 class="thanks-heading">
        <span class="thanks-heading__line">Thank you</span>
        <span class="thanks-heading__line thanks-heading__line--indent">for shopping</span>
      </h1>
    </div>
  </section>

  <section class="postcard postcard--back">
    <div class="postcard__face">
      <h2 class="tips-heading">Hair Care Tips</h2>
      <ol class="tips-list">
        <li>1. Wash with lukewarm water.</li>
        <li>2. Condition correctly.</li>
        <li>3. Concentrate shampoo on the scalp.</li>
        <li>4. Be extra thorough with rinsing.</li>
        <li class="tips-list__gap">5. Don't dry of using a towel.</li>
        <li>6. Protect hair before heat styling.</li>
        <li>7. Blow-dry with a brush.</li>
        <li>8. Only straighten and curl dry hair.</li>
      </ol>
      <div class="contact contact--social"><span class="contact__dot"></span>@luna.kova.wigs__</div>
      <div class="contact contact--web">www.lunakovawigs.example</div>
    </div>
  </section>
</main>
</body>
</html>
```